Tolvik Commercial Cleaning is lookong for a new business card design.

A fresh new design that's professional and stylish. We need a serious upgrade to our business cards. I have included pictures of our existing ones. Our clients include professional individuals and business owners. We woupdblike something professional and upbeat. Please have fun and see what you come uo with.

Target Market(s)

Property managers, business owners, facility managers and other similar professionals

Industry/Entity Type

Janitorial

Contact Information for Business Card

Name, cell, office number, email, web address

Font styles to use
Sans Serif

Colors

Designer to choose colors to be used in the design.

Requirements
Must have
• please use the green color in our logo
Nice to have
• Bar code
Should not have
• Address

```html
<!DOCTYPE html>
<html lang="en">
<head>
<meta charset="utf-8">
<title>Tolvik Commercial Cleaning – Business Card</title>
<link href="https://fonts.googleapis.com/css2?family=Montserrat:wght@400;600;700&display=swap" rel="stylesheet">
<style>
  :root {
    --brand-green: #41b05a;
    --ink: #333333;
    --paper: #ffffff;
    --backdrop: #e4e0da;
  }
  * { margin: 0; padding: 0; box-sizing: border-box; }
  html, body {
    width: 900px; height: 1200px; overflow: hidden;
    background: var(--backdrop);
    font-family: "Montserrat", Arial, sans-serif;
  }
  .canvas { position: relative; width: 900px; height: 1200px; }
  .card {
    position: absolute; left: 80px; width: 742px; height: 440px;
    border-radius: 40px;
    box-shadow: 0 4px 10px rgba(0,0,0,0.35);
  }
  .card-front { top: 132px; background: var(--paper); }
  .card-back { top: 638px; background: var(--brand-green); }

  .brand-block {
    position: absolute; left: 55px; top: 148px; width: 320px;
    text-align: center; color: var(--brand-green); font-weight: 700;
  }
  .brand-name { font-size: 84px; line-height: 1; letter-spacing: -1px; }
  .brand-tagline { font-size: 21px; margin-top: 22px; }

  .divider {
    position: absolute; left: 391px; top: 164px; width: 2px; height: 136px;
    background: var(--brand-green);
  }
  .contact-block { position: absolute; left: 437px; top: 162px; color: var(--ink); }
  .person-name { font-size: 25px; font-weight: 700; color: var(--brand-green); }
  .person-title { font-size: 16px; margin-top: 4px; }
  .contact-list { list-style: none; margin-top: 20px; }
  .contact-list li {
    display: flex; align-items: center; gap: 10px;
    font-size: 16px; line-height: 22px;
  }
  .contact-list svg { width: 14px; height: 14px; fill: var(--brand-green); flex: none; }

  .back-brand {
    position: absolute; left: 0; right: 0; top: 150px;
    text-align: center; color: var(--paper); font-weight: 700;
  }
  .back-brand .brand-name { font-size: 110px; }
  .back-brand .brand-tagline { font-size: 28px; margin-top: 24px; }
</style>
</head>
<body>
<main class="canvas">
  <section class="card card-front">
    <div class="brand-block">
      <div class="brand-name">Tolvik</div>
      <div class="brand-tagline">Commercial Cleaning</div>
    </div>
    <div class="divider"></div>
    <div class="contact-block">
      <div class="person-name">Marta Kellen</div>
      <div class="person-title">CEO &amp; Founder</div>
      <ul class="contact-list">
        <li>
          <svg viewBox="0 0 16 16"><path d="M2 5c0-2 2-3 6-3s6 1 6 3v1h-3V5H5v1H2zM4 7h8l2 6v1H2v-1zM8 9a2 2 0 1 0 0 4 2 2 0 0 0 0-4z"/></svg>
          (37) 555-0182
        </li>
        <li>
          <svg viewBox="0 0 16 16"><path d="M1 3h14v1.5L8 9 1 4.5zM1 6.3l7 4.5 7-4.5V13H1z"/></svg>
          marta@tolvikcleaning.com
        </li>
        <li>
          <svg viewBox="0 0 16 16"><circle cx="8" cy="8" r="7"/><path d="M5 4l3 2-1 3-2-1zM10 9l2 1-1 3-2-1z" fill="#ffffff"/></svg>
          www.tolvikcleaning.com
        </li>
      </ul>
    </div>
  </section>

  <section class="card card-back">
    <div class="back-brand">
      <div class="brand-name">Tolvik</div>
      <div class="brand-tagline">Commercial Cleaning</div>
    </div>
  </section>
</main>
</body>
</html>
```